Create a new business card

I’m looking to update my business card to make it match the rest of my brand. I will include my current website as well as what my vehicle designs look like, etc..
What my business currently services
Weekly maintenance pool openings / closings
Equipment repair, including pumps, heaters, salt systems, filters, etc.
We install automatic covers and maintain them as well as provide preventative maintenance

I would like to include my name.
Dorian Pelkin.
My title
Owner
My email
Dorian@tidewellnx.com
4015827160
Www.tidewellnx.com

```html
<!DOCTYPE html>
<html lang="en">
<head>
<meta charset="utf-8">
<title>Tidewell Pool Service – Business Card</title>
<link href="https://fonts.googleapis.com/css2?family=Poppins:wght@400;600&family=Kaushan+Script&display=swap" rel="stylesheet">
<style>
  :root {
    --navy: #1d2d69;
    --navy-deep: #16245a;
    --sky: #29abe2;
    --orange: #e5612a;
    --ink: #1b1b1b;
    --paper: #ffffff;
    --paper-shade: #eeeff1;
    --backdrop: #121212;
  }
  * { margin: 0; padding: 0; box-sizing: border-box; }
  html, body {
    width: 1200px; height: 1122px; overflow: hidden;
    background: var(--backdrop);
    font-family: "Poppins", sans-serif;
  }
  .canvas {
    position: relative; width: 1200px; height: 1122px;
  }
  .card {
    position: absolute; left: 220px; width: 760px; height: 434px;
    border-radius: 26px; overflow: hidden;
  }
  .card-front {
    top: 100px;
    background: radial-gradient(ellipse at 50% 45%, var(--navy) 0%, var(--navy-deep) 100%);
    display: flex; align-items: center; justify-content: center;
  }
  .brand {
    display: flex; align-items: center; gap: 18px;
    color: var(--paper); font-weight: 600; font-size: 44px; letter-spacing: 0.5px;
  }
  .brand-dot {
    width: 40px; height: 40px; border-radius: 50%; background: var(--sky);
  }
  .card-back {
    top: 588px;
    background: linear-gradient(160deg, var(--paper) 0%, var(--paper-shade) 55%, var(--paper) 100%);
  }
  .identity {
    position: absolute; left: 70px; top: 118px; width: 300px; text-align: right;
  }
  .person-name {
    font-family: "Kaushan Script", cursive; color: var(--navy);
    font-size: 50px; line-height: 1.1;
  }
  .person-title {
    color: var(--sky); font-size: 24px; font-weight: 400; margin-top: 2px;
  }
  .divider {
    position: absolute; left: 392px; top: 108px; width: 3px; height: 130px;
    background: var(--orange);
  }
  .contact-list {
    position: absolute; left: 420px; top: 104px; list-style: none;
  }
  .contact-item {
    display: flex; align-items: center; gap: 14px;
    color: var(--ink); font-size: 22px; line-height: 44px;
  }
  .contact-item.phone { font-size: 26px; font-weight: 400; }
  .contact-icon { width: 22px; height: 22px; flex: none; }
  .services {
    position: absolute; left: 0; right: 0; top: 300px; text-align: center;
    color: var(--navy); font-weight: 600; font-size: 19px; letter-spacing: 1px;
    line-height: 36px; text-transform: uppercase;
  }
  .tick {
    display: inline-block; width: 20px; height: 20px; vertical-align: -3px; margin: 0 6px;
  }
</style>
</head>
<body>
<main class="canvas">
  <section class="card card-front" aria-label="Card front">
    <div class="brand">
      <span class="brand-dot"></span>
      <span class="brand-name">Tidewell Pool Service</span>
    </div>
  </section>

  <section class="card card-back" aria-label="Card back">
    <div class="identity">
      <p class="person-name">Dorian Pelkin</p>
      <p class="person-title">Owner</p>
    </div>
    <span class="divider"></span>
    <ul class="contact-list">
      <li class="contact-item phone">
        <svg class="contact-icon" viewBox="0 0 24 24"><path fill="var(--sky)" d="M6.6 10.8a15.1 15.1 0 0 0 6.6 6.6l2.2-2.2c.3-.3.7-.4 1-.2 1.1.4 2.3.6 3.6.6.6 0 1 .4 1 1V20c0 .6-.4 1-1 1A17 17 0 0 1 3 4c0-.6.4-1 1-1h3.5c.6 0 1 .4 1 1 0 1.3.2 2.5.6 3.6.1.3 0 .7-.2 1z"/></svg>
        (401) 582-7160
      </li>
      <li class="contact-item">
        <svg class="contact-icon" viewBox="0 0 24 24"><rect x="2" y="5" width="20" height="14" rx="1.5" fill="var(--sky)"/><path d="M3 6l9 7 9-7" fill="none" stroke="#fff" stroke-width="1.6"/></svg>
        Dorian@tidewellnx.com
      </li>
      <li class="contact-item">
        <svg class="contact-icon" viewBox="0 0 24 24"><circle cx="12" cy="12" r="10" fill="var(--sky)"/><path d="M2 12h20M12 2c3 3 3 17 0 20M12 2c-3 3-3 17 0 20" fill="none" stroke="#fff" stroke-width="1.4"/></svg>
        www.tidewellnx.com
      </li>
    </ul>
    <div class="services">
      <p>Pool Openings/Closings
        <svg class="tick" viewBox="0 0 20 20"><circle cx="10" cy="10" r="10" fill="var(--orange)"/><path d="M5.5 10.5l3 3 6-6.5" fill="none" stroke="#fff" stroke-width="2.2"/></svg>
        Equipment Repair</p>
      <p>Including Pumps
        <svg class="tick" viewBox="0 0 20 20"><circle cx="10" cy="10" r="10" fill="var(--orange)"/><path d="M5.5 10.5l3 3 6-6.5" fill="none" stroke="#fff" stroke-width="2.2"/></svg>
        Heaters
        <svg class="tick" viewBox="0 0 20 20"><circle cx="10" cy="10" r="10" fill="var(--orange)"/><path d="M5.5 10.5l3 3 6-6.5" fill="none" stroke="#fff" stroke-width="2.2"/></svg>
        Salt Systems
        <svg class="tick" viewBox="0 0 20 20"><circle cx="10" cy="10" r="10" fill="var(--orange)"/><path d="M5.5 10.5l3 3 6-6.5" fill="none" stroke="#fff" stroke-width="2.2"/></svg>
        Filters, Etc.</p>
    </div>
  </section>
</main>
</body>
</html>
```